Kelo Wave Mint Business cards

Logo, tag line and photo on card
Agent Name
Title
Address
Phone number
Email
Website
Make logo on one side large by rotating  to portrait format.  Keep the background of the logo white.

Contact Information for Business Card
Slogan; Making Every Wave Count

```html
<!DOCTYPE html>
<html lang="en">
<head>
<meta charset="utf-8">
<title>Kelo Wave Mint – Business Cards</title>
<link rel="stylesheet" href="https://fonts.googleapis.com/css2?family=Montserrat:wght@300;400;600;700;800&display=swap">
<style>
  :root {
    --page-bg: #e4e3e5;
    --navy: #02266a;
    --red: #c01d2e;
    --white: #ffffff;
    --faint: #e7eaf2;
    --photo-top: #9a9a9a;
    --photo-bottom: #3f3f42;
  }
  * { box-sizing: border-box; margin: 0; padding: 0; }
  html, body {
    width: 1200px; height: 1108px; overflow: hidden;
    background: var(--page-bg);
    font-family: "Montserrat", sans-serif;
  }
  .card { position: absolute; overflow: hidden; }

  /* Front */
  .card-front {
    left: 228px; top: 68px; width: 757px; height: 435px;
    background: var(--red);
  }
  .front-band {
    position: absolute; left: 0; top: 0; width: 100%; height: 260px;
    background: var(--navy);
  }
  .brand-box {
    position: absolute; left: 134px; top: 21px; width: 141px; height: 172px;
    background: var(--white);
    display: flex; flex-direction: column; justify-content: center; align-items: center;
    color: var(--navy); font-weight: 800; font-size: 36px; line-height: 1.02;
    letter-spacing: -0.5px;
  }
  .tagline {
    position: absolute; left: 33px; top: 213px;
    color: var(--white); font-weight: 600; font-size: 26.5px;
  }
  .contact-list {
    position: absolute; left: 33px; top: 277px; list-style: none;
    color: var(--white); font-weight: 300; font-size: 20.5px;
  }
  .contact-list li { display: flex; align-items: center; height: 30px; }
  .contact-list svg { width: 22px; height: 22px; margin-right: 16px; flex: none; }
  .address {
    position: absolute; left: 33px; top: 374px;
    color: var(--white); font-weight: 300; font-size: 20.5px; line-height: 30px;
  }
  .portrait {
    position: absolute; left: 463px; top: 32px; width: 228px; height: 284px;
    background: var(--white); padding: 5px;
  }
  .portrait-fill {
    width: 100%; height: 100%;
    background: linear-gradient(180deg, var(--photo-top), var(--photo-bottom));
  }
  .person {
    position: absolute; left: 463px; top: 344px; width: 228px; text-align: center;
    color: var(--white);
  }
  .person-name { font-weight: 700; font-size: 24px; letter-spacing: 1.2px; }
  .person-title { font-weight: 400; font-size: 16.5px; letter-spacing: 1px; margin-top: 2px; }

  /* Back */
  .card-back {
    left: 210px; top: 575px; width: 779px; height: 444px;
    background: var(--white);
  }
  .brand-rotated {
    position: absolute; left: 205px; top: 215px; width: 0; height: 0;
  }
  .brand-rotated-text {
    position: absolute; left: -130px; top: -140px; width: 260px; height: 280px;
    transform: rotate(90deg);
    display: flex; flex-direction: column; justify-content: center;
    color: var(--navy); font-weight: 800; font-size: 88px; line-height: 0.98;
    letter-spacing: -2px;
  }
  .brand-faint {
    position: absolute; left: 412px; top: 10px; width: 346px; height: 431px;
    display: flex; flex-direction: column; justify-content: center; align-items: center;
    color: var(--faint); font-weight: 800; font-size: 100px; line-height: 1.15;
    letter-spacing: -2px;
  }
</style>
</head>
<body>

<section class="card card-front">
  <div class="front-band"></div>
  <div class="brand-box"><span>Kelo</span><span>Wave</span><span>Mint</span></div>
  <p class="tagline">Making Every Wave Count</p>

  <ul class="contact-list">
    <li>
      <svg viewBox="0 0 24 24" fill="none" stroke="#fff" stroke-width="1.8" stroke-linecap="round" stroke-linejoin="round" aria-hidden="true">
        <path d="M5 3h3l2 5-2 1.5a11 11 0 0 0 6.5 6.5L16 14l5 2v3a2 2 0 0 1-2 2A17 17 0 0 1 3 5a2 2 0 0 1 2-2z"/>
        <path d="M14 3a7 7 0 0 1 7 7M14 7a3 3 0 0 1 3 3"/>
      </svg>055-210 348 617
    </li>
    <li>
      <svg viewBox="0 0 24 24" fill="none" stroke="#fff" stroke-width="1.8" stroke-linejoin="round" aria-hidden="true">
        <rect x="2" y="5" width="20" height="14"/>
        <path d="M2 5l10 8 10-8M2 19l7.5-7M22 19l-7.5-7"/>
      </svg>hello@kelowavemint.com
    </li>
    <li>
      <svg viewBox="0 0 24 24" fill="none" stroke="#fff" stroke-width="1.8" aria-hidden="true">
        <circle cx="12" cy="12" r="10"/>
        <ellipse cx="12" cy="12" rx="4.5" ry="10"/>
        <path d="M2 12h20M4 6.5h16M4 17.5h16"/>
      </svg>www.kelowavemint.com
    </li>
  </ul>
  <p class="address">88, Harbor Lane Street<br>30781, Country name</p>

  <div class="portrait">
    <div class="portrait-fill" role="img" aria-label="Portrait photo of the managing director"></div>
  </div>
  <div class="person">
    <p class="person-name">DANIEL MERCER</p>
    <p class="person-title">MANAGING DIRECTOR</p>
  </div>
</section>

<section class="card card-back">
  <div class="brand-rotated">
    <div class="brand-rotated-text"><span>Kelo</span><span>Wave</span><span>Mint</span></div>
  </div>
  <div class="brand-faint" aria-hidden="true"><span>Kelo</span><span>Wave</span><span>Mint</span></div>
</section>

</body>
</html>
```